Rebrand stationary with recently completed logo design

Need new business cards, thank you cards, letterhead, envelopes and presentation folders. The designs will be sent to a separate production firm so I need the files to be print ready.

My contact info
Reko Haliburn

Office 604-318-5047
Fax 604-371-8054

Email reko@glazemark.ca
website www.glazemark.ca

315-14720 62nd Avenue,
Langley, BC, V2K 3R8

Target Market(s)

Homeowners, businesses and contractors

Industry/Entity Type

Business

Font styles to use
Sans Serif

Colors
34a7d7

Requirements
Must have
• Like to have one side of the business card a solid color with the logo in all white. The side with all the text to be a white background
• I find the current blue on the front of the card with the white logo too dark.
Should not have
• Gradient colors

```html
<!DOCTYPE html>
<html lang="en">
<head>
<meta charset="utf-8">
<title>Glazemark Business Card</title>
<link rel="stylesheet" href="https://fonts.googleapis.com/css2?family=Source+Sans+3:wght@400;600&display=swap">
<style>
  :root {
    --backdrop: #1f1f20;
    --card-white: #f1f1f1;
    --brand-blue: #0e97d8;
    --pattern-blue: #1b9ddb;
    --slate: #46515a;
    --ink-grey: #555b60;
    --text-white: #ffffff;
  }
  * { margin: 0; padding: 0; box-sizing: border-box; }
  html, body {
    width: 1200px; height: 960px; overflow: hidden;
    background: var(--backdrop);
    font-family: "Source Sans 3", "Helvetica Neue", Arial, sans-serif;
  }
  .stage { position: relative; width: 1200px; height: 960px; }

  .card {
    position: absolute; width: 600px; height: 342px;
    box-shadow: 0 4px 10px rgba(0,0,0,0.55);
    overflow: hidden;
  }
  .card-front { left: 302px; top: 129px; background: var(--card-white); }
  .card-back { left: 299px; top: 488px; background: var(--brand-blue); }

  .brand-lockup {
    position: absolute; left: 0; right: 0; top: 92px;
    display: flex; align-items: center; justify-content: center; gap: 16px;
  }
  .brand-square { width: 34px; height: 34px; background: var(--slate); }
  .brand-name {
    font-size: 46px; font-weight: 400; letter-spacing: 1px;
    color: var(--slate); line-height: 1;
  }

  .contact-band {
    position: absolute; left: 0; top: 196px; width: 600px; height: 96px;
    display: flex;
  }
  .band-identity {
    width: 298px; height: 100%; background: var(--brand-blue);
    color: var(--text-white); text-align: right;
    padding: 18px 26px 0 0;
  }
  .band-divider { width: 2px; height: 100%; background: var(--card-white); }
  .band-reach {
    flex: 1; height: 100%; background: var(--slate);
    color: var(--text-white); padding: 22px 0 0 24px;
  }
  .person-name { font-size: 19px; font-weight: 600; line-height: 22px; }
  .address-line { font-size: 14px; line-height: 19px; }
  .reach-line {
    display: flex; align-items: center; gap: 9px;
    font-size: 14px; line-height: 19px;
  }
  .reach-line svg { width: 13px; height: 13px; fill: var(--text-white); }

  .website {
    position: absolute; left: 0; right: 0; top: 307px;
    text-align: center; font-size: 14px; letter-spacing: 5.5px;
    color: var(--ink-grey);
  }
  .website b { font-weight: 600; }

  .back-field {
    position: absolute; inset: 0; background: var(--pattern-blue);
  }
  .back-brand {
    position: absolute; right: 38px; bottom: 30px;
    display: flex; align-items: center; gap: 10px;
  }
  .back-brand .brand-square { width: 22px; height: 22px; background: var(--text-white); }
  .back-brand .brand-name { font-size: 28px; color: var(--text-white); }
</style>
</head>
<body>
<main class="stage">
  <section class="card card-front">
    <div class="brand-lockup">
      <span class="brand-square"></span>
      <span class="brand-name">GLAZEMARK</span>
    </div>

    <div class="contact-band">
      <div class="band-identity">
        <p class="person-name">Reko Haliburn</p>
        <p class="address-line">315-14720 62nd Avenue</p>
        <p class="address-line">Langley, BC, V2K 3R8</p>
      </div>
      <div class="band-divider"></div>
      <div class="band-reach">
        <p class="reach-line">
          <svg viewBox="0 0 16 16" aria-hidden="true"><path d="M3.6 1.2l2.3 2.6-1.3 1.9c.9 2 2.5 3.6 4.6 4.6l1.9-1.3 2.6 2.3-1.5 2.3C7.4 15 1 8.6 1.3 3z"/></svg>
          604-318-5047
        </p>
        <p class="reach-line">
          <svg viewBox="0 0 16 16" aria-hidden="true"><path d="M4 1h8v4H4z M1 6h14v6h-3v3H4v-3H1z M5 10v4h6v-4z"/></svg>
          604-371-8054
        </p>
        <p class="reach-line">
          <svg viewBox="0 0 16 16" aria-hidden="true"><path d="M1 3h14v1L8 9 1 4z M1 5.5l7 5 7-5V13H1z"/></svg>
          reko@glazemark.ca
        </p>
      </div>
    </div>

    <p class="website">www.<b>glazemark</b>.ca</p>
  </section>

  <section class="card card-back">
    <div class="back-field" role="img" aria-label="Repeating brand symbol pattern in light blue tones"></div>
    <div class="back-brand">
      <span class="brand-square"></span>
      <span class="brand-name">GLAZEMARK</span>
    </div>
  </section>
</main>
</body>
</html>
```